Meridale Real Estate

We are looking for help with web design for a new company that is revolutionizing the real estate world on the listing side: by charing per hour for top level professional real estate services. We would like the concept to be simple, clean and easily understood.
Updates

We want this website to actually function, not just a static design.

Industry/Entity Type

Real Estate

```html
<!DOCTYPE html>
<html lang="en">
<head>
<meta charset="utf-8">
<title>Meridale Real Estate</title>
<link href="https://fonts.googleapis.com/css2?family=PT+Sans:wght@400;700&family=Roboto:wght@700&display=swap" rel="stylesheet">
<style>
:root{
  --ink:#000;
  --white:#fff;
  --accent:#4cc3f0;
  --link:#5ec8f4;
  --panel:rgba(40,40,44,.78);
  --footer:#1b1c1e;
  --muted:#cfd3d6;
  --sky-top:#8fb4cf;
  --sky-mid:#b9cfdc;
  --green:#4f7a3c;
  --green-dark:#2f5528;
}
*{margin:0;padding:0;box-sizing:border-box}
html,body{width:1200px;height:689px;overflow:hidden}
body{position:relative;font-family:'PT Sans',Arial,sans-serif;color:var(--white);background:var(--footer)}
.hero-photo{position:absolute;left:0;top:0;width:1200px;height:657px;
  background:linear-gradient(180deg,var(--sky-top) 0%,var(--sky-mid) 42%,#a9bfb5 55%,#6f9160 68%,var(--green) 82%,var(--green-dark) 100%)}
.nav-bar{position:absolute;left:0;top:43px;width:1200px;height:53px;background:var(--ink)}
.nav{position:absolute;left:479px;top:43px;height:53px;display:flex;list-style:none}
.nav li{height:53px;display:flex;align-items:center;justify-content:center;font-size:12.5px;font-weight:700;letter-spacing:.3px;border-left:1px solid #333}
.nav .commercial{width:108px}
.nav .residential{width:97px}
.nav .farm{width:57px}
.nav .vacant{width:104px}
.nav .contact{width:78px;background:var(--accent);border-left:none}
.logo{position:absolute;left:316px;top:16px;width:102px;height:102px;border-radius:50%;background:var(--ink);
  display:flex;flex-direction:column;align-items:center;justify-content:center;text-align:center;font-size:12px;font-weight:700;letter-spacing:1.5px;line-height:15px}
.social{position:absolute;display:flex;gap:2px}
.social span{width:15px;height:15px;display:block}
.social .s1{background:#3b5a9a}.social .s2{background:#2fa9e0}.social .s3{background:#f28c22}
.social.top{left:736px;top:15px}
.search{position:absolute;left:793px;top:15px;width:107px;height:16px;background:var(--white);border:1px solid #9aa;font-size:9px;font-style:italic;color:#555;padding:2px 0 0 28px}
.search svg{position:absolute;left:6px;top:2px}
.chevron{position:absolute;left:906px;top:18px}
.headline{position:absolute;left:336px;top:172px;width:330px;font-family:'Roboto',Arial,sans-serif;font-weight:700;font-size:18.5px;line-height:23px;text-shadow:0 1px 2px rgba(0,0,0,.35)}
.side-arrow{position:absolute;top:267px;width:44px;height:38px;background:var(--accent);display:flex;align-items:center;justify-content:center}
.side-arrow.prev{left:0}.side-arrow.next{left:1156px}
.panel{position:absolute;background:var(--panel)}
.news{left:277px;top:331px;width:647px;height:105px}
.news-title{position:absolute;left:11px;top:6px;font-size:9px;font-weight:700}
.news-arrow{position:absolute;top:371px;width:21px;height:24px;background:var(--ink);display:flex;align-items:center;justify-content:center}
.news-arrow.prev{left:268px}.news-arrow.next{left:912px}
.photo{position:absolute}
.story{position:absolute;top:353px;width:165px;font-size:9px;line-height:11.3px}
.story h3,.tile-caption,.location h3{font-size:9px;font-weight:700}
.story a,.location a{color:var(--link);text-decoration:none}
.listings{left:277px;top:448px;width:390px;height:103px}
.tile-caption{position:absolute;top:528px}
.location{left:677px;top:448px;width:247px;height:103px}
.location .info{position:absolute;left:14px;top:19px;font-size:9px;line-height:11px}
.map{position:absolute;left:800px;top:457px;width:115px;height:84px;background:linear-gradient(135deg,#efe9dc,#dcd6c6);border:2px solid #ddd}
.dots{position:absolute;left:542px;top:591px;display:flex;gap:7px}
.dots span{width:8px;height:8px;border-radius:50%;background:var(--white)}
.dots .active{background:var(--accent)}
.footer{position:absolute;left:0;top:657px;width:1200px;height:32px;background:var(--footer);border-top:2px solid var(--accent)}
.legal{position:absolute;left:284px;top:5px;font-size:7.5px;line-height:11px;color:var(--muted)}
.legal a{color:var(--muted)}
.follow{position:absolute;left:825px;top:10px;font-size:8.5px;color:var(--muted)}
.social.bottom{left:865px;top:665px}
</style>
</head>
<body>
<div class="hero-photo" role="img" aria-label="Photograph of modern high-rise residential towers above landscaped green parkland and a river under a pale blue sky"></div>

<div class="nav-bar"></div>
<ul class="nav">
  <li class="commercial">COMMERCIAL</li>
  <li class="residential">RESIDENTIAL</li>
  <li class="farm">FARM</li>
  <li class="vacant">VACANT LAND</li>
  <li class="contact">CONTACT US</li>
</ul>
<div class="logo"><span>MERIDALE</span><span>REAL ESTATE</span></div>

<div class="social top"><span class="s1"></span><span class="s2"></span><span class="s3"></span></div>
<div class="search">
  <svg width="10" height="10" viewBox="0 0 10 10"><circle cx="4" cy="4" r="3" fill="none" stroke="#888" stroke-width="1.3"/><line x1="6.2" y1="6.2" x2="9" y2="9" stroke="#888" stroke-width="1.5"/></svg>
  Search
</div>
<svg class="chevron" width="12" height="8" viewBox="0 0 12 8"><polyline points="1,1 6,6 11,1" fill="none" stroke="#fff" stroke-width="1.5"/></svg>

<h1 class="headline">Lorem ipsum dolor sit amet, consectetur adipisicing elit, sed do eiusmod tempor incididunt ut labore et dolore magna aliqua.</h1>

<div class="side-arrow prev"><svg width="8" height="10" viewBox="0 0 8 10"><polyline points="6,1 2,5 6,9" fill="none" stroke="#fff" stroke-width="1.5"/></svg></div>
<div class="side-arrow next"><svg width="8" height="10" viewBox="0 0 8 10"><polyline points="2,1 6,5 2,9" fill="none" stroke="#fff" stroke-width="1.5"/></svg></div>

<section class="panel news"><h2 class="news-title">NEWS</h2></section>
<div class="news-arrow prev"><svg width="6" height="9" viewBox="0 0 6 9"><polyline points="5,1 1,4.5 5,8" fill="none" stroke="#fff" stroke-width="1.5"/></svg></div>
<div class="news-arrow next"><svg width="6" height="9" viewBox="0 0 6 9"><polyline points="1,1 5,4.5 1,8" fill="none" stroke="#fff" stroke-width="1.5"/></svg></div>

<div class="photo" style="left:324px;top:353px;width:100px;height:62px;background:linear-gradient(180deg,#9cc0dc,#8a6f5a 60%,#4e6a3a)" role="img" aria-label="Photo of a large Victorian-style house"></div>
<article class="story" style="left:444px">
  <h3>LOREN IPSUM</h3>
  <p>Lorem ipsum dolor sit amet, consectetur adipisicing elit, sed do eiusmod tempor incididunt ut labore et dolore magna aliqua.</p>
  <a href="#">Read more</a>
</article>
<div class="photo" style="left:613px;top:353px;width:102px;height:62px;background:linear-gradient(135deg,#e8e2d6,#b9ab92 60%,#7d7060)" role="img" aria-label="Photo of a bright living room interior"></div>
<article class="story" style="left:739px">
  <h3>LOREN IPSUM</h3>
  <p>Lorem ipsum dolor sit amet, consectetur adipisicing elit, sed do eiusmod tempor incididunt ut labore et dolore magna aliqua.</p>
  <a href="#">Read more</a>
</article>

<section class="panel listings"></section>
<div class="photo" style="left:296px;top:467px;width:91px;height:56px;background:linear-gradient(180deg,#dfe6ec,#8d99a4)" role="img" aria-label="Photo of a modern office building"></div>
<div class="photo" style="left:424px;top:467px;width:92px;height:56px;background:linear-gradient(180deg,#3b2a20,#c87a33 45%,#8a5a2a)" role="img" aria-label="Photo of farmland at sunset"></div>
<div class="photo" style="left:556px;top:467px;width:92px;height:56px;background:linear-gradient(180deg,#cfe0ee,#8fa6b8 60%,#6a7d6a)" role="img" aria-label="Photo of a commercial tower"></div>
<span class="tile-caption" style="left:296px">LOREN IPSUM</span>
<span class="tile-caption" style="left:424px">LOREN IPSUM</span>
<span class="tile-caption" style="left:556px">LOREN IPSUM</span>

<section class="panel location">
  <div class="info">
    <h3>LOCATION</h3>
    <p>HARLOW PROPERTY GROUP<br>1185 Alder Creek Road<br>Fairbrook, CA 95510<br>BRE#02783340</p>
    <a href="#">View map location</a>
  </div>
</section>
<div class="map" role="img" aria-label="Street map showing the office location"></div>

<div class="dots"><span></span><span class="active"></span><span></span><span></span><span></span><span></span><span></span></div>

<footer class="footer">
  <p class="legal">Copyright © 2013 Harlow Property Group | <a href="#">Privacy Policy</a> | <a href="#">Terms and Conditions</a><br>© Copyright Harlow Property Group. All rights reserved.</p>
  <span class="follow">Follow us:</span>
</footer>
<div class="social bottom"><span class="s1"></span><span class="s2"></span><span class="s3"></span></div>
</body>
</html>
```